BrivoTerna. Lantern of the Steady Harvest. Business card

Professional business card for BrivoTerna (Lantern of the Steady Harvest)
My rationale: Strategy-> Execution-> Results-> Value that lead to the BrivoTerna name: We put the Lantern of the Steady Harvest.
We deliver value to our customers helping them at defining a good strategy (cyan arrow). 90% of well formulated strategies fail due to poor execution so we also consider strategical execution very important (green arrow). Due to the execution we obtain the results (blue arrow). Finally, the results provide feedback to redefine strategy, and the new strategy has to be executed and new results obtained providing new feedback and on and on. It's like a wheel that finally, must create corporate value: value for shareholders, staholders, employees, providers...-

Target Market(s)

CEOs and steering comitees , invewrnent funds

Industry/Entity Type

Business Consultant

Contact Information for Business Card

Teodoro Vinsquel
CEO & Founder
teodoro.vinsquel@brivoterna-example.com
Mobile: +34 655.803.912
www.brivoterna-example.com

Colors

Designer to choose colors to be used in the design.

Requirements
Nice to have
• Nice to hace the words: Strategy, execution, results
• Nice to vave the claim: Lantern of the Steady Harvest
• The three colors should be shown:
• cyan for STRATEGY
• green for EXECUTION
• blue for RESULTS
Should not have
• Complete black background

```html
<!DOCTYPE html>
<html lang="en">
<head>
<meta charset="utf-8">
<title>BrivoTerna — Business Card</title>
<link rel="stylesheet" href="https://fonts.googleapis.com/css2?family=Open+Sans:wght@400;600;700;800&display=swap">
<style>
  :root {
    --royal-blue: #0a2d9c;
    --deep-blue: #0b2f8f;
    --lime: #8cc63f;
    --cyan: #29a8e0;
    --paper: #ffffff;
    --ink: #222222;
    --backdrop: #e9ebef;
  }
  * { box-sizing: border-box; margin: 0; padding: 0; }
  html, body {
    width: 1200px; height: 900px; overflow: hidden;
    background: var(--backdrop);
    font-family: "Open Sans", sans-serif;
  }
  .canvas { position: relative; width: 1200px; height: 900px; }
  .card {
    position: absolute; width: 600px; height: 343px;
    border-radius: 22px; overflow: hidden;
    box-shadow: 0 14px 30px rgba(10, 30, 80, 0.18);
  }
  .card--front { left: 90px; top: 70px; background: var(--paper); }
  .card--back { left: 510px; top: 480px; background: var(--royal-blue); }
  .card__shapes { position: absolute; inset: 0; width: 100%; height: 100%; }

  .brand-name {
    position: absolute; font-weight: 800; letter-spacing: -0.5px;
    display: flex; align-items: center; gap: 10px; white-space: nowrap;
  }
  .brand-name__dot { width: 14px; height: 14px; border-radius: 50%; background: currentColor; }
  .card--front .brand-name { left: 46px; top: 118px; font-size: 36px; line-height: 48px; color: var(--deep-blue); }
  .card--back .brand-name {
    left: 0; right: 0; top: 140px; justify-content: center;
    font-size: 54px; color: var(--paper);
  }

  .holder { position: absolute; left: 48px; top: 196px; white-space: nowrap; }
  .holder__name { font-size: 21px; line-height: 28px; font-weight: 700; color: var(--deep-blue); }
  .holder__role { font-size: 14px; line-height: 20px; color: var(--ink); }

  .contact {
    position: absolute; right: 24px; top: 140px;
    list-style: none; text-align: right; color: var(--paper);
    font-size: 11px; line-height: 24px; white-space: nowrap;
  }
  .contact__item { display: flex; justify-content: flex-end; align-items: center; gap: 7px; }
  .contact__icon { width: 11px; height: 11px; flex: none; }

  .pillars {
    position: absolute; right: 24px; top: 218px;
    font-size: 13px; line-height: 18px; font-weight: 800; letter-spacing: 0.5px;
    color: var(--cyan); text-transform: uppercase; white-space: nowrap;
  }
  .pillars__sep { margin: 0 5px; }
</style>
</head>
<body>
<main class="canvas">

  <section class="card card--front" aria-label="Business card front">
    <svg class="card__shapes" viewBox="0 0 600 343" aria-hidden="true">
      <path d="M380,0 C370,190 280,275 0,300 L0,343 L600,343 L600,0 Z" fill="var(--lime)"/>
      <path d="M392,0 C384,196 292,288 0,314 L0,343 L600,343 L600,0 Z" fill="var(--paper)"/>
      <path d="M398,0 C390,200 298,294 0,320 L0,343 L600,343 L600,0 Z" fill="var(--royal-blue)"/>
    </svg>

    <div class="brand-name"><span class="brand-name__dot"></span>BrivoTerna</div>

    <div class="holder">
      <p class="holder__name">Teodoro Vinsquel</p>
      <p class="holder__role">CEO &amp; Founder</p>
    </div>

    <ul class="contact">
      <li class="contact__item">+34 655.803.912
        <svg class="contact__icon" viewBox="0 0 12 12"><rect x="3" y="0.5" width="6" height="11" rx="1.2" fill="none" stroke="currentColor"/></svg>
      </li>
      <li class="contact__item">www.brivoterna-example.com
        <svg class="contact__icon" viewBox="0 0 12 12"><circle cx="6" cy="6" r="5.2" fill="none" stroke="currentColor"/><path d="M1,6 H11 M6,1 C3,4 3,8 6,11 M6,1 C9,4 9,8 6,11" fill="none" stroke="currentColor" stroke-width="0.8"/></svg>
      </li>
      <li class="contact__item">teodoro.vinsquel@brivoterna-example.com
        <svg class="contact__icon" viewBox="0 0 12 12"><rect x="0.5" y="2.5" width="11" height="7" fill="none" stroke="currentColor"/><path d="M0.5,2.5 L6,7 L11.5,2.5" fill="none" stroke="currentColor"/></svg>
      </li>
    </ul>

    <p class="pillars">Results<span class="pillars__sep">•</span>Execution<span class="pillars__sep">•</span>Strategy</p>
  </section>

  <section class="card card--back" aria-label="Business card back">
    <div class="brand-name"><span class="brand-name__dot"></span>BrivoTerna</div>
  </section>

</main>
</body>
</html>
```